Request for Business Card Design

Hi. My name is Marlene, I am looking for a new business card design for my company, Quarrow Signal Instruments, LLC. I really like the design you did for Tarsel Venture and was hoping you could do something similar using our full logo and our mark. I am also open to any raised texture design using our mark. I have attached our full logo, which would need to be somewhere on the card, as well as the mark in both outline and full form, as well as our brand colors / guide. The card does not have to be white, as long as our logo and mark appear. I actually like darker colored business cards more, but am open to all options. If you are interested in working with me, please let me know. We would also take the business card design into letterhead design if you can do that.

```html
<!DOCTYPE html>
<html lang="en">
<head>
<meta charset="utf-8">
<title>Quarrow Signal Instruments – Business Cards</title>
<link rel="stylesheet" href="https://fonts.googleapis.com/css2?family=Barlow:wght@400;700&display=swap">
<style>
  :root {
    --backdrop: #7f97b8;
    --front-red: #e23331;
    --front-red-deep: #d92a2a;
    --back-blue: #2ea3c6;
    --back-blue-light: #43b2d2;
    --ink-white: #ffffff;
    --soft-white: rgba(255,255,255,0.14);
  }
  * { margin: 0; padding: 0; box-sizing: border-box; }
  html, body { width: 1200px; height: 876px; overflow: hidden; }
  body {
    background: var(--backdrop);
    font-family: "Barlow", Arial, sans-serif;
    color: var(--ink-white);
    position: relative;
  }
  .card {
    position: absolute;
    top: 290px;
    width: 520px;
    height: 297px;
    border-radius: 3px;
    overflow: hidden;
    box-shadow: 0 10px 24px rgba(30,45,80,0.35);
  }
  .card--back { left: 60px; background: linear-gradient(135deg, var(--back-blue-light), var(--back-blue)); }
  .card--front { left: 620px; background: linear-gradient(135deg, var(--front-red), var(--front-red-deep)); }

  .brand { display: flex; align-items: center; gap: 12px; }
  .brand__dot { width: 34px; height: 34px; border-radius: 50%; background: var(--ink-white); flex: none; }
  .brand__name { font-weight: 700; font-size: 30px; letter-spacing: 2px; line-height: 1; text-transform: uppercase; }
  .brand__tagline { font-size: 9.5px; letter-spacing: 0.6px; text-transform: uppercase; margin-top: 4px; }

  .card--front .brand { position: absolute; left: 44px; top: 78px; }
  .front__decor { position: absolute; right: -70px; bottom: -90px; width: 280px; height: 280px; border-radius: 50%; background: var(--soft-white); }

  .card--back .brand { position: absolute; left: 130px; top: 92px; }
  .card--back .brand__name { font-size: 26px; }
  .holder { position: absolute; right: 40px; top: 30px; text-align: right; }
  .holder__name { font-size: 18px; letter-spacing: 1px; text-transform: uppercase; }
  .holder__name b { font-weight: 700; }
  .holder__role { font-size: 12px; margin-top: 2px; }

  .contact-rail { position: absolute; left: 0; right: 0; top: 212px; height: 2px; background: var(--ink-white); }
  .contact { position: absolute; top: 202px; display: flex; flex-direction: column; align-items: center; text-align: center; font-size: 12px; line-height: 1.3; }
  .contact__icon { width: 22px; height: 22px; border-radius: 50%; background: var(--ink-white); display: flex; align-items: center; justify-content: center; margin-bottom: 8px; }
  .contact--phone { left: 40px; }
  .contact--address { left: 190px; }
  .contact--email { left: 340px; }
</style>
</head>
<body>
  <section class="card card--back" aria-label="Business card back">
    <div class="holder">
      <p class="holder__name"><b>Dorian</b> Pell</p>
      <p class="holder__role">Director</p>
    </div>
    <div class="brand">
      <span class="brand__dot"></span>
      <div>
        <p class="brand__name">Quarrow</p>
        <p class="brand__tagline">Signal Instruments</p>
      </div>
    </div>
    <div class="contact-rail"></div>
    <div class="contact contact--phone">
      <span class="contact__icon"><svg width="12" height="12" viewBox="0 0 12 12"><rect x="3" y="1" width="6" height="10" rx="1.2" fill="none" stroke="#2ea3c6" stroke-width="1.4"/></svg></span>
      <p>+000 48210 3375</p>
    </div>
    <div class="contact contact--address">
      <span class="contact__icon"><svg width="12" height="12" viewBox="0 0 12 12"><path d="M6 11 C3 7 2.5 5.5 2.5 4.5 A3.5 3.5 0 0 1 9.5 4.5 C9.5 5.5 9 7 6 11Z" fill="#2ea3c6"/></svg></span>
      <p>14 Harbour Lane<br>Singapore, 4410</p>
    </div>
    <div class="contact contact--email">
      <span class="contact__icon"><svg width="12" height="12" viewBox="0 0 12 12"><rect x="1.5" y="3" width="9" height="6.5" fill="none" stroke="#2ea3c6" stroke-width="1.3"/><path d="M1.5 3 L6 7 L10.5 3" fill="none" stroke="#2ea3c6" stroke-width="1.3"/></svg></span>
      <p>hello@quarrowsignal.com</p>
    </div>
  </section>

  <section class="card card--front" aria-label="Business card front">
    <div class="front__decor"></div>
    <div class="brand">
      <span class="brand__dot"></span>
      <div>
        <p class="brand__name">Quarrow</p>
        <p class="brand__tagline">Signal Instruments</p>
      </div>
    </div>
  </section>
</body>
</html>
```